Local fast-growing company in the service sector

We are looking for a modern business card design, which should also appear on our letterheads

Target Market(s)

Private and industrial sectors

Contact Information for Business Card

Vorname Name
Kellberger Str. 18
70419 Lindenfeld
Tel.: 07146-839214-0
Name@agentur-kvtl.de

Colors
9d9d9d
919191
aaaaaa

Requirements
Must have
• The logo (file) in silver

```html
<!DOCTYPE html>
<html lang="de">
<head>
<meta charset="utf-8">
<title>KVTL – Visitenkarte</title>
<link rel="stylesheet" href="https://fonts.googleapis.com/css2?family=Mulish:wght@400;600;800&display=swap">
<style>
  :root {
    --page-bg: #d9d9d9;
    --frost-top: #f4f4f4;
    --frost-bottom: #dcdcdc;
    --dark-top: #4a4a4a;
    --dark-bottom: #2b2b2b;
    --silver: #aaaaaa;
    --silver-mid: #9d9d9d;
    --silver-deep: #919191;
    --text-light: #e6e6e6;
    --text-soft: #c9c9c9;
  }
  html, body {
    margin: 0;
    padding: 0;
    width: 1200px;
    height: 969px;
    overflow: hidden;
    background: var(--page-bg);
    font-family: "Mulish", Arial, sans-serif;
  }
  .canvas {
    position: relative;
    width: 1200px;
    height: 969px;
  }
  .business-card {
    position: absolute;
    left: 100px;
    top: 200px;
    width: 1000px;
    height: 570px;
    border-radius: 34px;
    overflow: hidden;
    box-shadow: 0 18px 40px rgba(0,0,0,0.18);
  }
  .card-background {
    position: absolute;
    inset: 0;
  }
  .brand {
    position: absolute;
    left: 76px;
    top: 235px;
    display: flex;
    align-items: center;
    gap: 18px;
  }
  .brand-mark {
    width: 70px;
    height: 70px;
    background: var(--silver-deep);
  }
  .brand-name {
    font-weight: 800;
    font-size: 84px;
    line-height: 1;
    letter-spacing: 1px;
    color: var(--silver-deep);
  }
  .contact-block {
    position: absolute;
    right: 66px;
    top: 178px;
    text-align: right;
    color: var(--text-light);
  }
  .person-name {
    font-size: 38px;
    font-weight: 600;
    margin: 0 0 14px;
    letter-spacing: 0.5px;
  }
  .address {
    font-size: 21px;
    line-height: 1.45;
    color: var(--text-soft);
    margin: 0 0 26px;
    font-style: normal;
  }
  .contact-list {
    list-style: none;
    margin: 0;
    padding: 0;
    font-size: 21px;
    line-height: 1.6;
    color: var(--text-soft);
  }
  .contact-list li {
    display: flex;
    justify-content: flex-end;
    align-items: center;
    gap: 14px;
  }
  .contact-icon {
    width: 20px;
    height: 20px;
    fill: var(--text-soft);
  }
</style>
</head>
<body>
<div class="canvas">
  <div class="business-card">
    <svg class="card-background" width="1000" height="570" viewBox="0 0 1000 570">
      <defs>
        <linearGradient id="frost" x1="0" y1="0" x2="0" y2="1">
          <stop offset="0" stop-color="var(--frost-top)"/>
          <stop offset="1" stop-color="var(--frost-bottom)"/>
        </linearGradient>
        <linearGradient id="dark" x1="0" y1="0" x2="1" y2="1">
          <stop offset="0" stop-color="var(--dark-top)"/>
          <stop offset="1" stop-color="var(--dark-bottom)"/>
        </linearGradient>
        <linearGradient id="silverBand" x1="0" y1="0" x2="0" y2="1">
          <stop offset="0" stop-color="var(--silver)"/>
          <stop offset="0.5" stop-color="#e2e2e2"/>
          <stop offset="1" stop-color="var(--silver-deep)"/>
        </linearGradient>
      </defs>
      <rect class="frost-panel" width="1000" height="570" fill="url(#frost)"/>
      <path class="silver-band" d="M340 0 H1000 V570 H340 L575 310 Q595 285 575 260 Z" fill="url(#silverBand)"/>
      <path class="dark-panel" d="M370 0 H1000 V570 H370 L600 310 Q620 285 600 260 Z" fill="url(#dark)"/>
    </svg>

    <div class="brand">
      <div class="brand-mark"></div>
      <div class="brand-name">KVTL</div>
    </div>

    <div class="contact-block">
      <p class="person-name">Lukas Brenner</p>
      <address class="address">Kellberger Str. 18<br>70419 Lindenfeld</address>
      <ul class="contact-list">
        <li>07146-839214-0
          <svg class="contact-icon" viewBox="0 0 24 24"><path d="M6.6 10.8a15.1 15.1 0 0 0 6.6 6.6l2.2-2.2c.3-.3.7-.4 1-.2 1.1.4 2.3.6 3.6.6.6 0 1 .4 1 1V20c0 .6-.4 1-1 1A17 17 0 0 1 3 4c0-.6.4-1 1-1h3.5c.6 0 1 .4 1 1 0 1.3.2 2.5.6 3.6.1.3 0 .7-.2 1z"/></svg>
        </li>
        <li>Name@agentur-kvtl.de
          <svg class="contact-icon" viewBox="0 0 24 24"><path d="M2 5h20v14H2z M4 7v.4l8 5 8-5V7l-8 5z" fill-rule="evenodd"/></svg>
        </li>
        <li>www.agentur-kvtl.de
          <svg class="contact-icon" viewBox="0 0 24 24"><circle cx="12" cy="12" r="10"/><path d="M2 12h20M12 2c3 3 3 17 0 20M12 2c-3 3-3 17 0 20" stroke="var(--dark-bottom)" stroke-width="1.5" fill="none"/></svg>
        </li>
      </ul>
    </div>
  </div>
</div>
</body>
</html>
```